Webdesign für Brenner Flusskraft
Zielgruppe
Ansprechpartner für Planung und Errichtung von Stromerzeugung durch erneuerbare Energien. Alle Interessen im privaten, teilöffentlichen und öffentlichen Bereich, die mittel- und langfristig umweltschonenden Strom nutzen wollen.
Aufgabenstellung
- Farben bitte in den Unternehmensfarben Blau/Weiß mit einem kleinen Anteil Orange
- Bilder nach Möglichkeit bitte nur eigene (siehe Anhang)
- klare und übersichtliche Struktur
- KEIN Abklatsch der alten Webseite

```html
<!DOCTYPE html>
<html lang="de">
<head>
<meta charset="utf-8">
<title>Brenner Flusskraft – Unsere Leistungen</title>
<link rel="stylesheet" href="https://fonts.googleapis.com/css2?family=Poppins:wght@500;600;700&family=Roboto:wght@300;400;500&family=Roboto+Condensed:wght@400&display=swap">
<style>
  :root {
    --navy: #02007f;
    --navy-text: #0a0a8c;
    --bar-bg: #f2f2f2;
    --orange: #ff8a00;
    --white: #ffffff;
    --body-text: #333344;
    --wave-light: #a3a3d6;
    --wave-mid: #5a58b4;
    --career-blue: #7aa9f7;
  }
  * { box-sizing: border-box; margin: 0; padding: 0; }
  html, body { width: 1200px; height: 579px; overflow: hidden; }
  body { position: relative; background: var(--navy); font-family: "Roboto", sans-serif; }

  .top-bar {
    position: absolute; left: 0; top: 0; width: 1200px; height: 26px;
    background: var(--bar-bg); color: var(--navy-text);
  }
  .top-bar__mail { position: absolute; left: 223px; top: 7px; display: flex; align-items: center; gap: 11px;
    font-family: "Poppins", sans-serif; font-weight: 500; font-size: 9px; }
  .top-bar__mail span { position: relative; top: -3px; }
  .top-bar__claim { position: absolute; left: 0; width: 1190px; top: 10px; text-align: center;
    font-family: "Poppins", sans-serif; font-weight: 500; font-size: 9.5px; letter-spacing: .1px; }
  .top-bar__address { position: absolute; left: 821px; top: 4px; display: flex; gap: 12px; }
  .top-bar__address .lines { line-height: 1.1; }
  .top-bar__address .street { font-family: "Poppins", sans-serif; font-weight: 500; font-size: 9.5px; }
  .top-bar__address .city { font-family: "Roboto Condensed", sans-serif; font-size: 8.5px; }

  .section-title {
    position: absolute; top: 24px; left: 0; width: 1190px; text-align: center;
    font-family: "Poppins", sans-serif; font-weight: 700; font-size: 20px; color: var(--white);
  }

  .waves { position: absolute; left: 0; top: 470px; width: 1200px; height: 109px; }

  .service-card {
    position: absolute; top: 78px; width: 212px; height: 408px; background: var(--white);
    text-align: center;
  }
  .service-card--water { left: 257px; }
  .service-card--solar { left: 489px; }
  .service-card--mobility { left: 720px; }
  .service-card__image { height: 135px; width: 100%; }
  .service-card--water .service-card__image { background: linear-gradient(160deg, #4a4a3c 0%, #8a8470 35%, #dfe3e4 60%, #5c6670 100%); }
  .service-card--solar .service-card__image { background: linear-gradient(180deg, #dcc6e6 0%, #e8d8c8 30%, #8aa04a 45%, #5a6c9c 60%, #7a7fb4 80%, #6a8c40 100%); }
  .service-card--mobility .service-card__image { background: linear-gradient(120deg, #8a6a30 0%, #3a3a48 40%, #1c3c5c 65%, #0e1a2c 100%); }
  .service-card__button {
    position: absolute; top: 123px; left: 50%; transform: translateX(-50%);
    width: 84px; height: 22px; background: var(--orange); color: var(--white);
    font-family: "Poppins", sans-serif; font-weight: 600; font-size: 6.8px; letter-spacing: .6px;
    line-height: 22px;
  }
  .service-card__title {
    margin-top: 27px; font-family: "Roboto", sans-serif; font-weight: 500; font-size: 12.5px;
    color: var(--navy-text); letter-spacing: .2px;
  }
  .service-card__text {
    margin: 5px auto 0; width: 180px; font-weight: 300; font-size: 9px; line-height: 17px; color: var(--body-text);
  }
  .service-card__text + .service-card__text { margin-top: 9px; }

  .career-banner {
    position: absolute; left: 257px; top: 505px; width: 675px; height: 80px;
    border-radius: 4px; overflow: hidden; background: var(--career-blue);
  }
  .career-banner__photo { position: absolute; left: 0; top: 0; width: 338px; height: 100%;
    background: linear-gradient(90deg, #6a6e74 0%, #c8ccd0 40%, #8a8c90 70%, #3a3c40 100%); }
  .career-banner__icon { position: absolute; left: 309px; top: 18px; }
  .career-banner__label { position: absolute; left: 400px; top: 39px; color: var(--white);
    font-family: "Poppins", sans-serif; font-weight: 500; font-size: 7.5px; letter-spacing: 2px; }
  .career-banner__mail { position: absolute; left: 400px; top: 52px; color: var(--white);
    font-family: "Poppins", sans-serif; font-weight: 600; font-size: 12.5px; }
</style>
</head>
<body>
  <header class="top-bar">
    <div class="top-bar__mail">
      <svg width="13" height="10" viewBox="0 0 13 10"><rect x="0" y="0" width="13" height="10" rx="1.5" fill="var(--navy-text)"/><path d="M1 1.5 L6.5 5.5 L12 1.5" stroke="#f2f2f2" stroke-width="1.3" fill="none"/></svg>
      <span>info@brenner-flusskraft.de</span>
    </div>
    <div class="top-bar__claim">IHR PROFI FÜR ERNEUERBARE ENERGIEN</div>
    <div class="top-bar__address">
      <svg width="12" height="16" viewBox="0 0 12 16"><path d="M6 0 C2.7 0 0 2.6 0 5.9 C0 10 6 16 6 16 C6 16 12 10 12 5.9 C12 2.6 9.3 0 6 0 Z" fill="var(--navy-text)"/><circle cx="6" cy="6" r="2.3" fill="#f2f2f2"/></svg>
      <div class="lines"><div class="street">Erlenweg 14</div><div class="city">09322 Talheim</div></div>
    </div>
  </header>

  <h1 class="section-title">Unsere Leistungen</h1>

  <svg class="waves" viewBox="0 0 1200 109" preserveAspectRatio="none">
    <path d="M0 12 C150 -4 300 2 420 40 L800 40 C950 70 1080 20 1200 8 L1200 109 L0 109 Z" fill="var(--wave-mid)"/>
    <path d="M0 32 C120 16 240 18 330 38 L900 90 C1000 70 1100 45 1200 35 L1200 109 L0 109 Z" fill="var(--wave-light)"/>
    <path d="M0 66 C120 50 230 50 300 58 L900 109 L0 109 Z M1000 109 C1080 90 1150 80 1200 76 L1200 109 Z" fill="var(--white)"/>
  </svg>

  <article class="service-card service-card--water">
    <div class="service-card__image" role="img" aria-label="Foto: Staudamm mit tosendem Wasser im Sonnenlicht"></div>
    <div class="service-card__button">MEHR ERFAHREN</div>
    <h2 class="service-card__title">WASSERKRAFT</h2>
    <p class="service-card__text">Als Betreiber von Wasserkraftanlagen lassen wir eigene wertvollen Erfahrungen in unsere Projekte einfließen und stehen Ihnen immer als kompetenter Ansprechpartner in allen Fragen rund um die Wasserkraft zur Verfügung.</p>
    <p class="service-card__text">Mit unseren modularen Steuerungen können wir in kurzer Zeit auf Ihre Wünsche Reagieren und halten gleichzeitig Ausfallkosten und Wartungsaufwand minimal.</p>
  </article>

  <article class="service-card service-card--solar">
    <div class="service-card__image" role="img" aria-label="Foto: Solarpark mit Windrädern im Hintergrund"></div>
    <div class="service-card__button">MEHR ERFAHREN</div>
    <h2 class="service-card__title">PHOTOVOLTAIK</h2>
    <p class="service-card__text">Als Experten im Bereich regenerative Energien finden Sie mit uns Ihren Partner zur Verwirklichung Ihrer Potovoltaikprojekte. Von der Errichtung eines Solarparks im Megawattbereich bis zur autarken Inselllösung im Eigenheim stehen wir Ihnen mit unserem Expertenwissen zur Seite.</p>
    <p class="service-card__text">Wir helfen Ihnen den Eigenverbrauch Ihrer PV-Anlage zu steigern.</p>
  </article>

  <article class="service-card service-card--mobility">
    <div class="service-card__image" role="img" aria-label="Foto: Elektroauto beim Laden am Abend"></div>
    <div class="service-card__button">MEHR ERFAHREN</div>
    <h2 class="service-card__title">ELEKTROMOBILITÄT</h2>
    <p class="service-card__text">ist zum Tagesgespräch geworden. Wir sprechen nicht nur darüber, wir gestalten die Elektromobilität.</p>
    <p class="service-card__text">Wir sind Ihr Mobilitätsdienstleister und begleiten Sie auf neuen Wegen.</p>
    <p class="service-card__text">Ob eine Testfahrt in einem Elektrofahrzeug, die Langzeitmiete oder das Errichten eines Elektroladeparkplatzes – bei uns sind Sie richtig aufgehoben.</p>
  </article>

  <section class="career-banner">
    <div class="career-banner__photo" role="img" aria-label="Foto: Geschäftsleute beim Handschlag"></div>
    <svg class="career-banner__icon" width="62" height="62" viewBox="0 0 62 62">
      <circle cx="31" cy="31" r="30" fill="none" stroke="rgba(255,255,255,.35)" stroke-width="1"/>
      <circle cx="29" cy="29" r="28" fill="var(--white)"/>
      <g transform="rotate(-18 29 29)" fill="none" stroke="#2f7ff0" stroke-width="2">
        <rect x="16" y="20" width="26" height="17" rx="1"/>
        <path d="M16 20 L29 30 L42 20 M16 37 L25 28 M42 37 L33 28"/>
      </g>
    </svg>
    <div class="career-banner__label">◢ KARRIERE</div>
    <div class="career-banner__mail">bewerbung@brenner-flusskraft.de</div>
  </section>
</body>
</html>
```